Unique Business Card Design

Unique Business Card design for our orthotic and prosthetic company. Our logo is on our website, color is light blue. Unique shape (artificial leg shaped, vertical, etc..) preferred. Logo, business name, individual name and basic demographics needed.

Industry/Entity Type

Business

Contact Information for Business Card

Logo, Industry, Phone # Logo, "Prosthetic & Orthotic Services" Place to add individual name and contact info

Colors
cee9f5

Requirements
Must have
• The icon must be there, placement of "Prosthetic & Orthotic Services" can be moved
Nice to have
• Like the mix of light blue, and a little darker blue. One design included the icons from my website which was a nice touch

```html
<!DOCTYPE html>
<html lang="en">
<head>
<meta charset="utf-8">
<title>Limbworks Inc. Business Card</title>
<link href="https://fonts.googleapis.com/css2?family=Open+Sans:wght@600;700&family=Roboto:ital,wght@0,400;1,400&family=Signika:wght@600&family=Libre+Baskerville:ital@1&display=swap" rel="stylesheet">
<style>
  :root {
    --brand-blue: #246399;
    --brand-blue-deep: #1f5a8c;
    --charcoal: #3a3d40;
    --ink: #333638;
    --paper: #f6f6f6;
    --white: #ffffff;
    --backdrop: #e8e8e8;
  }
  * { margin: 0; padding: 0; box-sizing: border-box; }
  html, body { width: 1200px; height: 576px; overflow: hidden; background: var(--backdrop); }
  .stage { position: relative; width: 1200px; height: 576px; }

  .card { position: absolute; top: 139px; width: 484px; height: 292px; border-radius: 7px; overflow: hidden; }
  .card--front { left: 82px; background: linear-gradient(180deg, var(--brand-blue) 0%, var(--brand-blue-deep) 100%); color: var(--white); }
  .card--back { left: 602px; width: 480px; height: 289px; background: var(--paper); color: var(--ink); }

  .mark { position: absolute; border-radius: 50%; }
  .card--front .mark { left: 91px; top: 106px; width: 79px; height: 77px; background: var(--white); }
  .card--back .mark { left: 204px; top: 34px; width: 64px; height: 62px; background: var(--brand-blue); }

  .wordmark { position: absolute; font-family: "Open Sans", sans-serif; font-weight: 700; white-space: nowrap; letter-spacing: 0.2px; }
  .card--front .wordmark { left: 190px; top: 108px; font-size: 23px; }
  .card--back .wordmark { left: 284px; top: 42px; font-size: 18px; color: var(--brand-blue); }

  .rule { position: absolute; height: 2px; }
  .card--front .rule { left: 190px; top: 140px; width: 202px; background: var(--white); }
  .card--back .rule { left: 284px; top: 67px; width: 163px; height: 1.5px; background: var(--brand-blue); }

  .tagline { position: absolute; font-family: "Libre Baskerville", serif; font-style: italic; white-space: nowrap; }
  .card--front .tagline { left: 204px; top: 144px; font-size: 12px; }
  .card--back .tagline { left: 294px; top: 71px; font-size: 9.5px; color: var(--brand-blue); }

  .front-phone { position: absolute; left: 214px; top: 158px; font-family: "Open Sans", sans-serif; font-weight: 700; font-size: 21px; letter-spacing: 1px; }

  .person { position: absolute; left: 25px; top: 136px; }
  .person__name { font-family: "Signika", sans-serif; font-weight: 600; font-size: 18px; color: var(--brand-blue); }
  .person__title { font-family: "Roboto", sans-serif; font-style: italic; font-size: 11.5px; margin-top: 1px; }

  .contact { position: absolute; font-family: "Roboto", sans-serif; font-size: 12.5px; white-space: nowrap; }
  .contact svg { position: absolute; left: -22px; top: 1px; width: 12px; height: 12px; fill: var(--brand-blue); }
  .contact--mobile { left: 47px; top: 182px; }
  .contact--mobile svg { left: -22px; }
  .contact--phone { left: 253px; top: 138px; }
  .contact--fax { left: 253px; top: 155px; }
  .contact--email { left: 253px; top: 172px; }
  .contact--address { left: 230px; top: 193px; }

  .footer-band { position: absolute; left: 0; top: 252px; width: 480px; height: 37px; }
  .website { position: absolute; left: 230px; top: 264px; font-family: "Roboto", sans-serif; font-size: 12.5px; color: var(--white); }
</style>
</head>
<body>
<main class="stage">

  <section class="card card--front" aria-label="Card front">
    <div class="mark"></div>
    <div class="wordmark">LIMBWORKS INC.</div>
    <div class="rule"></div>
    <div class="tagline">Prosthetic &amp; Orthotic Services</div>
    <div class="front-phone">555.201.4400</div>
  </section>

  <section class="card card--back" aria-label="Card back">
    <div class="mark"></div>
    <div class="wordmark">LIMBWORKS INC.</div>
    <div class="rule"></div>
    <div class="tagline">Prosthetic &amp; Orthotic Services</div>

    <div class="person">
      <div class="person__name">Miriam Castell</div>
      <div class="person__title">Orthotist/Prosthetist</div>
    </div>

    <div class="contact contact--mobile">
      <svg viewBox="0 0 12 12" aria-hidden="true"><path d="M3 0h6a1 1 0 0 1 1 1v10a1 1 0 0 1-1 1H3a1 1 0 0 1-1-1V1a1 1 0 0 1 1-1zm0.8 1.5v7.5h4.4V1.5zM6 9.8a0.7 0.7 0 1 0 0 1.4 0.7 0.7 0 0 0 0-1.4z"/></svg>
      555-0187342
    </div>
    <div class="contact contact--phone">
      <svg viewBox="0 0 12 12" aria-hidden="true"><path d="M1 3.5C1 2 3 1 6 1s5 1 5 2.5V5H8.5V3.8H3.5V5H1zM3 6h6l1.5 5h-9z"/></svg>
      555.201.4400
    </div>
    <div class="contact contact--fax">
      <svg viewBox="0 0 12 12" aria-hidden="true"><path d="M3 0h6v3H3zM1 4h10v5H9V7H3v2H1zM3.5 8h5v4h-5z"/></svg>
      555.201.4419
    </div>
    <div class="contact contact--email">
      <svg viewBox="0 0 12 12" aria-hidden="true"><path d="M6 0a6 6 0 1 0 0 12A6 6 0 0 0 6 0zm0 1.2c.6 0 1.3 1.4 1.5 3.3h-3C4.7 2.6 5.4 1.2 6 1.2zM1.3 5.5h2.2c0 .4 0 .7.1 1H1.3a4.8 4.8 0 0 1 0-1zm3.2 0h3c0 .4 0 .7-.1 1h-2.8c0-.3-.1-.6-.1-1zm4 0h2.2a4.8 4.8 0 0 1 0 1H8.4c.1-.3.1-.6.1-1zM4.5 7.5h3C7.3 9.4 6.6 10.8 6 10.8S4.7 9.4 4.5 7.5z"/></svg>
      mcastell@limbworksinc.com
    </div>
    <div class="contact contact--address">240 Harbor Ave. Newport, RI 02840</div>

    <svg class="footer-band" viewBox="0 0 480 37" aria-hidden="true">
      <rect x="0" y="19" width="214" height="18" fill="var(--charcoal)"/>
      <polygon points="214,0 480,0 480,37 190,37" fill="var(--brand-blue)"/>
    </svg>
    <div class="website">www.limbworksinc.com</div>
  </section>

</main>
</body>
</html>
```